High end Electrical/home automation Business Card

Need a card for a high end electrical and home automation company utilising the existing logo.
Phone
Email
Website

Like black look with raised detail. Don’t necessarily need to keep colour of logo it could be made grayscale or white etc

Target Market(s)

High end clients

Contact Information for Business Card

Brightmoor Electrical

Requirements
Must have
• Logo, phone, email, website, address

High end look
Nice to have
• Black background card
Raised font
Should not have
• Lots of colour

```html
<!DOCTYPE html>
<html lang="en">
<head>
<meta charset="utf-8">
<title>Brightmoor Electrical – Business Card</title>
<link href="https://fonts.googleapis.com/css2?family=Montserrat:wght@400;500;600;800&display=swap" rel="stylesheet">
<style>
  :root{
    --backdrop:#adada9;
    --card:#353537;
    --card-deep:#2c2c2e;
    --accent:#0b8ed6;
    --ink:#ffffff;
    --ink-soft:#e6e6e6;
  }
  *{box-sizing:border-box;margin:0;padding:0}
  html,body{width:1200px;height:801px;overflow:hidden}
  body{
    background:var(--backdrop);
    font-family:"Montserrat",Arial,sans-serif;
    position:relative;
  }
  .card{
    position:absolute;
    top:250px;
    width:520px;
    height:297px;
    background:var(--card);
    border-bottom:4px solid var(--accent);
    border-left:2px solid var(--accent);
    box-shadow:0 14px 30px rgba(0,0,0,.28);
  }
  .card--front{left:50px}
  .card--back{left:630px}

  /* front */
  .brand{
    position:absolute;
    left:36px;
    top:0;
    width:210px;
    height:100%;
    display:flex;
    align-items:center;
    gap:10px;
  }
  .brand__dot{
    width:18px;height:18px;border-radius:50%;
    background:var(--accent);
    flex:none;
  }
  .brand__name{
    color:var(--ink);
    font-weight:800;
    font-size:19px;
    line-height:1.15;
    letter-spacing:-.2px;
  }
  .divider{
    position:absolute;
    left:262px;
    top:58px;
    width:1px;
    height:181px;
    background:var(--accent);
  }
  .contact{
    position:absolute;
    left:284px;
    top:58px;
    color:var(--ink-soft);
    font-size:11.5px;
    line-height:1.5;
  }
  .contact__name{
    color:var(--accent);
    font-weight:500;
    font-size:17px;
    letter-spacing:1.2px;
    text-transform:uppercase;
    line-height:1.2;
  }
  .contact__role{margin-bottom:10px}
  .contact__address{margin-bottom:10px}
  .contact__line{display:flex;align-items:center;gap:6px}
  .contact__line svg{width:9px;height:9px;flex:none}

  /* back */
  .pattern{
    position:absolute;inset:0;
    background:linear-gradient(135deg,#3a3a3c 0%,var(--card) 45%,var(--card-deep) 100%);
  }
  .emblem{
    position:absolute;
    left:50%;top:50%;
    transform:translate(-50%,-50%);
    display:flex;align-items:center;gap:7px;
    padding:6px 10px;
    background:var(--card);
  }
  .emblem__dot{width:10px;height:10px;border-radius:50%;background:var(--accent)}
  .emblem__name{color:var(--ink);font-weight:800;font-size:11px;letter-spacing:.3px}
</style>
</head>
<body>

<section class="card card--front" aria-label="Card front">
  <div class="brand">
    <span class="brand__dot"></span>
    <span class="brand__name">Brightmoor<br>Electrical</span>
  </div>
  <div class="divider"></div>
  <div class="contact">
    <p class="contact__name">Daniel Reyes</p>
    <p class="contact__role">Founder</p>
    <p class="contact__address">418 Alder Lane<br>Cedar Ridge, WA 99000</p>
    <p class="contact__line">
      <svg viewBox="0 0 10 10" aria-hidden="true"><path d="M2 1l2 2-1 1.2c.6 1.2 1.5 2.1 2.8 2.8L7 6l2 2-1.3 1.3C4.5 9 1 5.5.7 2.3z" fill="var(--accent)"/></svg>
      555 012 4830
    </p>
    <p class="contact__line">
      <svg viewBox="0 0 10 10" aria-hidden="true"><rect x=".8" y="2" width="8.4" height="6" fill="none" stroke="var(--accent)" stroke-width="1"/><path d="M.8 2l4.2 3.3L9.2 2" fill="none" stroke="var(--accent)" stroke-width="1"/></svg>
      hello@brightmoorelectrical.com
    </p>
    <p class="contact__line">
      <svg viewBox="0 0 10 10" aria-hidden="true"><circle cx="5" cy="5" r="4.2" fill="none" stroke="var(--accent)" stroke-width="1"/><path d="M.8 5h8.4M5 .8c-2.2 2.4-2.2 6 0 8.4M5 .8c2.2 2.4 2.2 6 0 8.4" fill="none" stroke="var(--accent)" stroke-width=".8"/></svg>
      brightmoorelectrical.com
    </p>
  </div>
</section>

<section class="card card--back" aria-label="Card back">
  <div class="pattern" role="img" aria-label="Raised tone-on-tone repeat pattern of the company emblem"></div>
  <div class="emblem">
    <span class="emblem__dot"></span>
    <span class="emblem__name">Brightmoor Electrical</span>
  </div>
</section>

</body>
</html>
```